Business Card Design

We have recently seen two business cards that caught our attention and think the designs would work for us. We are an accounting firm that serves small businesses in a variety of industries. Attached are the two business card that inspired us along with very rough layouts. We would like to see a professional layout using our company information.

Industry/Entity Type

Accounting

Contact Information for Business Card

Company Name - Marlowe Thistle
Address - 4182 Orlanby Lane, Suite 610, Houston, TX 77093
713-555-0187 - Main
281-555-0342 - Fax

Team Member Names, emails and phone numbers (see attachment)

```html
<!DOCTYPE html>
<html lang="en">
<head>
<meta charset="utf-8">
<title>Marlowe Thistle – Business Card</title>
<link href="https://fonts.googleapis.com/css2?family=Lato:wght@400;700;900&display=swap" rel="stylesheet">
<style>
  :root {
    --ink: #111111;
    --paper: #ffffff;
    --grey-tab: #c9c9c9;
    --grey-text: #8a8a8a;
    --backdrop: #e6e6e6;
  }
  html, body {
    margin: 0;
    width: 1200px;
    height: 482px;
    overflow: hidden;
    background: var(--backdrop);
    font-family: "Lato", Arial, sans-serif;
    color: var(--ink);
  }
  .business-card {
    position: absolute;
    left: 250px;
    top: 41px;
    width: 700px;
    height: 400px;
    background: var(--paper);
    box-shadow: 0 6px 18px rgba(0,0,0,0.18);
    overflow: hidden;
  }
  .card-frame {
    position: absolute;
    inset: 0;
  }
  .brand-mark {
    position: absolute;
    left: 56px;
    top: 92px;
    display: flex;
    align-items: center;
    gap: 12px;
    font-weight: 900;
    font-size: 22px;
    color: var(--ink);
  }
  .brand-mark .brand-square {
    width: 26px;
    height: 26px;
    background: var(--ink);
  }
  .company-block {
    position: absolute;
    left: 300px;
    top: 52px;
  }
  .company-name {
    margin: 0;
    font-weight: 900;
    font-size: 34px;
    letter-spacing: 1px;
    line-height: 1;
  }
  .company-address {
    margin: 6px 0 0;
    font-size: 12.5px;
  }
  .company-lines {
    display: flex;
    gap: 22px;
    margin-top: 6px;
    font-size: 16px;
    font-weight: 700;
  }
  .company-lines span {
    display: flex;
    align-items: center;
    gap: 6px;
  }
  .company-lines svg { width: 15px; height: 15px; }
  .person-block {
    position: absolute;
    right: 44px;
    top: 232px;
    text-align: right;
  }
  .person-name {
    margin: 0;
    font-weight: 900;
    font-size: 22px;
  }
  .person-role {
    margin: 2px 0 0;
    font-size: 14px;
    color: var(--grey-text);
  }
  .contact-list {
    position: absolute;
    left: 58px;
    top: 282px;
    margin: 0;
    padding: 0;
    list-style: none;
    font-size: 17px;
    font-weight: 700;
    line-height: 29px;
  }
  .contact-icons {
    position: absolute;
    left: 0;
    top: 278px;
    width: 40px;
    height: 96px;
  }
</style>
</head>
<body>
  <div class="business-card">
    <svg class="card-frame" viewBox="0 0 700 400" width="700" height="400" aria-hidden="true">
      <!-- top band with curved notch on the left -->
      <path d="M70 0 H700 V14 H110 Q90 14 84 8 Q78 0 70 0 Z" fill="var(--ink)"/>
      <!-- bottom band with curved notch on the right -->
      <path d="M0 384 H560 Q578 384 586 392 Q594 400 610 400 H0 Z" fill="var(--ink)"/>
      <!-- right grey tab -->
      <rect x="684" y="240" width="16" height="44" rx="4" fill="var(--grey-tab)"/>
      <!-- left grey tab behind icons -->
      <rect x="0" y="276" width="32" height="100" rx="5" fill="var(--grey-tab)"/>
    </svg>

    <div class="brand-mark"><span class="brand-square"></span>Marlowe Thistle</div>

    <div class="company-block">
      <h1 class="company-name">MARLOWE THISTLE</h1>
      <p class="company-address">4182 Orlanby Lane, Suite 610, Houston, TX 77093</p>
      <div class="company-lines">
        <span>
          <svg viewBox="0 0 16 16"><path d="M2 5 Q8 1 14 5 L12 7 L10 6 V5 H6 V6 L4 7 Z M4 8 H12 L13 14 H3 Z" fill="var(--ink)"/></svg>
          713-555-0187
        </span>
        <span>
          <svg viewBox="0 0 16 16"><rect x="4" y="2" width="8" height="4" fill="var(--ink)"/><rect x="1" y="6" width="14" height="6" rx="1" fill="var(--ink)"/><rect x="4" y="11" width="8" height="4" fill="var(--ink)"/></svg>
          281-555-0342
        </span>
      </div>
    </div>

    <div class="person-block">
      <p class="person-name">DELPHINE ARBOR</p>
      <p class="person-role">Account Manager</p>
    </div>

    <svg class="contact-icons" viewBox="0 0 40 96" aria-hidden="true">
      <path d="M9 14 Q16 9 23 14 L21 16 L19 15 V14 H13 V15 L11 16 Z M11 17 H21 L22 23 H10 Z" fill="var(--ink)"/>
      <rect x="12" y="38" width="8" height="14" rx="1.5" fill="none" stroke="var(--ink)" stroke-width="1.6"/>
      <rect x="9" y="68" width="14" height="10" fill="var(--ink)"/>
      <path d="M9 68 L16 74 L23 68" fill="none" stroke="var(--paper)" stroke-width="1.2"/>
    </svg>
    <ul class="contact-list">
      <li>713-555-0187</li>
      <li>832-555-0419</li>
      <li>darbor@marlowethistle.com</li>
    </ul>
  </div>
</body>
</html>
```